Business Card Design - Property Management & Real Estate Services

I need a business card design for my company that I can print ZEPLA Cards. The company is called Brindle Management Company. It is a property management and real estate company. The design has to be clean and modern. I need two versions. One for my employee and one for me. However, the design will be the same, just different text. You can get a feel for the company by looking at our website at www.brindlemanagement.example.

Industry/Entity Type

Property Management

Contact Information for Business Card

I will be using ZEPLA.com to print my cards. I will most likely use the rounded edges card. I need two versions, however, they will be the same design. I need one for me and my employee.

Colors
3276b5
33a6d7

Requirements
Must have
• Company Logo
• Name of person
• Property Management & Real Estate Service
• Phone
• Email
• Website
• Address
• A space to place a QR code

```html
<!DOCTYPE html>
<html lang="en">
<head>
<meta charset="utf-8">
<title>Brindle Management – Business Card</title>
<link href="https://fonts.googleapis.com/css2?family=Fira+Sans+Condensed:wght@600&family=Roboto:wght@400;500&display=swap" rel="stylesheet">
<style>
  :root {
    --page-bg: #e4e6e9;
    --card-bg: #f3f4f5;
    --brand-blue: #2c5ea3;
    --name-blue: #24508c;
    --band-blue: #2b5a9e;
    --band-line: #5a7fb5;
    --text-dark: #2b3038;
    --text-muted: #5b6370;
    --text-light: #dfe7f3;
    --qr-line: #b9c3d1;
  }
  * { margin: 0; padding: 0; box-sizing: border-box; }
  html, body {
    width: 1200px; height: 1054px; overflow: hidden;
    background: var(--page-bg);
    font-family: "Roboto", Arial, sans-serif;
  }
  .business-card {
    position: absolute; left: 100px; top: 227px;
    width: 1000px; height: 600px;
    background: var(--card-bg);
    border-radius: 26px;
    overflow: hidden;
    box-shadow: 0 10px 30px rgba(0,0,0,0.12);
  }
  .brand-lockup {
    position: absolute; left: 60px; top: 268px;
    width: 380px;
    text-align: center;
  }
  .brand-name {
    display: inline-flex; align-items: center; gap: 12px;
    font-family: "Roboto", Arial, sans-serif;
    font-weight: 500; font-size: 34px; line-height: 1;
    color: var(--brand-blue);
  }
  .brand-mark {
    width: 18px; height: 18px;
    background: var(--brand-blue);
  }
  .brand-tagline {
    margin-top: 16px;
    font-size: 16px; line-height: 1.3;
    color: var(--text-muted);
  }
  .person {
    position: absolute; left: 485px; top: 174px;
  }
  .person-name {
    font-family: "Fira Sans Condensed", "Arial Narrow", sans-serif;
    font-weight: 600; font-size: 37px;
    color: var(--name-blue);
  }
  .person-role {
    margin-top: 4px;
    font-size: 23px; color: var(--text-dark);
  }
  .contact-list {
    position: absolute; left: 485px; top: 308px;
    list-style: none;
  }
  .contact-list li {
    display: flex; align-items: center;
    height: 38px;
    font-size: 23px; color: var(--text-dark);
  }
  .contact-list svg {
    width: 20px; height: 20px; margin-right: 22px;
    fill: var(--text-dark);
  }
  .qr-space {
    position: absolute; right: 40px; top: 40px;
    width: 110px; height: 110px;
    border: 2px solid var(--qr-line);
    border-radius: 8px;
  }
  .band-rule {
    position: absolute; left: 0; right: 0; top: 533px;
    height: 3px; background: var(--band-line);
  }
  .address-band {
    position: absolute; left: 0; right: 0; top: 543px; bottom: 0;
    background: var(--band-blue);
    color: var(--text-light);
    font-size: 25px;
    display: flex; align-items: center; justify-content: center;
  }
</style>
</head>
<body>
  <div class="business-card">
    <div class="qr-space" role="img" aria-label="Space reserved for a QR code"></div>

    <div class="brand-lockup">
      <div class="brand-name"><span class="brand-mark"></span>Brindle Management</div>
      <div class="brand-tagline">Property Management &amp; Real Estate Services</div>
    </div>

    <div class="person">
      <div class="person-name">Marco L. Delgado</div>
      <div class="person-role">Founder</div>
    </div>

    <ul class="contact-list">
      <li>
        <svg viewBox="0 0 24 24" aria-hidden="true"><path d="M3 9c0-3 4-5 9-5s9 2 9 5v2h-5V9c-1-.6-2.4-1-4-1s-3 .4-4 1v2H3zM7 12h10l3 8H4z"/></svg>
        (305) 555-0148
      </li>
      <li>
        <svg viewBox="0 0 24 24" aria-hidden="true"><path d="M2 5h20v14H2zM4 7v.5l8 5.5 8-5.5V7zM4 10v7h16v-7l-8 5.5z"/></svg>
        marco@brindlemanagement.example
      </li>
      <li>
        <svg viewBox="0 0 24 24" aria-hidden="true"><path d="M12 2a10 10 0 1 0 0 20 10 10 0 0 0 0-20zm6.9 9h-3a15 15 0 0 0-1.3-6 8 8 0 0 1 4.3 6zM12 4c.9 1 2 3.5 2.1 7H9.9C10 7.5 11.1 5 12 4zM9.4 5a15 15 0 0 0-1.3 6h-3a8 8 0 0 1 4.3-6zM5.1 13h3a15 15 0 0 0 1.3 6 8 8 0 0 1-4.3-6zM12 20c-.9-1-2-3.5-2.1-7h4.2c-.1 3.5-1.2 6-2.1 7zm2.6-1a15 15 0 0 0 1.3-6h3a8 8 0 0 1-4.3 6z"/></svg>
        www.brindlemanagement.example
      </li>
    </ul>

    <div class="band-rule"></div>
    <div class="address-band">480 Harbor Point Ave #300 Miami, FL 33130</div>
  </div>
</body>
</html>
```